Business Card Design of an established Waste Management, Plastic Recycling and Renewable Energy Comp

We are looking for business card design for plastic card with holograms (Very similar to credit card). I will provide our logo (Quenbys). So the name on the business card will be our logo )Quenbys) + Environmental next to it, so it will read Quenbys Environmental. The font for Environmental does not to be the same as the font of the logo. The holograms will be used to display ISO14001 Certified (In normal credit card, normally on the holograms, they show nova or kelo). I will post the design requirements from the card printing company very shortly to make sure they can use the design for the plastic card.

Target Market(s)

Companies, Government Organizations, Corporations.

Industry/Entity Type

Business

Contact Information for Business Card

Motto (Under the logo): Let's Make It Right
Name: Leopold Maresca; Position: Business Manager; Address: Pelmore Landfill & Recycling Facility, Tressingham Rd, Maresby Downs, WA 6187; Ph: +61 8 5210 4738; Mob: +61 455 903 172; E: Leo@quenbysenvironmental-mail.com

Requirements
Must have
• Business Names: Quenbys Logo + Environmental word after the logo.
• Motto (Under the logo): Let's Make It Right
• All the Business Card Details above.
• Hologram Logo on the lower right corner which says: certification seal.
• Please remember the design will be printed on plastic card Not paper. The plastic crad is the same as credit card. Hope this helps. Thank You

```html
<!DOCTYPE html>
<html lang="en">
<head>
<meta charset="utf-8">
<title>Quenbys Environmental – Business Card</title>
<link href="https://fonts.googleapis.com/css2?family=Montserrat:wght@400;500;600;700&display=swap" rel="stylesheet">
<style>
  :root {
    --page-bg: #d9dde2;
    --card-bg: #f7f8f9;
    --card-edge: #c9ced4;
    --brand-blue: #1f7fc4;
    --brand-navy: #16508f;
    --ink: #3a3d42;
    --ink-strong: #2d3035;
    --holo-light: #e9edf1;
    --holo-mid: #b9c2cb;
  }
  * { margin: 0; padding: 0; box-sizing: border-box; }
  html, body { width: 846px; height: 1200px; overflow: hidden; }
  body {
    background: var(--page-bg);
    font-family: "Montserrat", sans-serif;
    color: var(--ink);
    position: relative;
  }
  .card {
    position: absolute;
    left: 122px;
    width: 602px;
    height: 334px;
    border-radius: 22px;
    background: linear-gradient(135deg, #ffffff 0%, var(--card-bg) 60%, #eef0f3 100%);
    border: 1px solid var(--card-edge);
    box-shadow: 0 8px 24px rgba(40, 50, 60, 0.12);
  }
  .card--front { top: 176px; }
  .card--back { top: 766px; }

  .brand {
    position: absolute;
    left: 34px;
    top: 36px;
    display: flex;
    align-items: center;
    gap: 14px;
  }
  .brand__dot {
    width: 70px; height: 70px;
    border-radius: 50%;
    background: var(--brand-blue);
  }
  .brand__words { line-height: 1; }
  .brand__name {
    font-size: 44px;
    font-weight: 700;
    color: var(--ink-strong);
    letter-spacing: 0.5px;
  }
  .brand__sub {
    font-size: 18px;
    font-weight: 600;
    color: var(--ink-strong);
    letter-spacing: 4.6px;
    margin-top: 6px;
  }
  .motto {
    font-size: 11px;
    font-weight: 500;
    color: var(--ink-strong);
    letter-spacing: 5.4px;
    margin-top: 6px;
  }

  .contact {
    position: absolute;
    left: 34px;
    top: 155px;
    font-size: 13.5px;
    line-height: 1.45;
  }
  .contact__name {
    font-size: 17px;
    font-weight: 600;
    color: var(--brand-blue);
  }
  .contact__role { margin-bottom: 10px; }
  .contact__line { display: flex; align-items: center; gap: 7px; }
  .contact__line svg { width: 12px; height: 12px; flex: none; }
  .contact__address { margin-top: 8px; line-height: 1.4; }

  .hologram {
    position: absolute;
    width: 120px; height: 120px;
    border-radius: 50%;
    background: radial-gradient(circle at 38% 35%, var(--holo-light) 0%, var(--holo-mid) 70%, #9ea8b3 100%);
    border: 3px solid var(--ink-strong);
    box-shadow: 0 0 0 34px var(--brand-blue), 0 0 0 38px var(--brand-navy);
  }
  .card--front .hologram { left: 392px; top: 132px; }
  .card--back .hologram { left: 88px; top: 134px; }

  .back-motto {
    position: absolute;
    left: 290px;
    top: 184px;
    font-size: 17px;
    font-weight: 500;
    letter-spacing: 6.4px;
    color: var(--ink-strong);
    white-space: nowrap;
  }
</style>
</head>
<body>

  <section class="card card--front">
    <div class="brand">
      <div class="brand__dot"></div>
      <div class="brand__words">
        <div class="brand__name">Quenbys</div>
        <div class="brand__sub">Environmental</div>
        <div class="motto">Let's Make It Right</div>
      </div>
    </div>

    <div class="contact">
      <div class="contact__name">Leopold Maresca</div>
      <div class="contact__role">Business Manager</div>
      <div class="contact__line">
        <svg viewBox="0 0 12 12" aria-hidden="true"><rect x="3" y="0.5" width="6" height="11" rx="1.2" fill="none" stroke="#1f7fc4" stroke-width="1.3"/><rect x="4.3" y="2" width="3.4" height="4.5" fill="#1f7fc4"/></svg>
        +61 455 903 172
      </div>
      <div class="contact__line">
        <svg viewBox="0 0 12 12" aria-hidden="true"><path d="M1 4.5 Q6 1 11 4.5 L10 6 L8 5 L8 4 Q6 3.4 4 4 L4 5 L2 6 Z" fill="#1f7fc4"/><rect x="2.5" y="6.5" width="7" height="4.5" rx="1" fill="#1f7fc4"/></svg>
        +61 8 5210 4738
      </div>
      <div class="contact__line">
        <svg viewBox="0 0 12 12" aria-hidden="true"><rect x="0.5" y="2.5" width="11" height="7" fill="#1f7fc4"/><path d="M0.5 2.5 L6 7 L11.5 2.5" fill="none" stroke="#fff" stroke-width="1"/></svg>
        Leo@quenbysenvironmental-mail.com
      </div>
      <div class="contact__address">
        Pelmore Landfill &amp; Recycling Facility,<br>
        Tressingham Rd, Maresby Downs, WA 6187
      </div>
    </div>

    <div class="hologram" role="img" aria-label="Certification seal hologram"></div>
  </section>

  <section class="card card--back">
    <div class="hologram" role="img" aria-label="Certification seal hologram"></div>
    <div class="back-motto">Let's Make It Right</div>
  </section>

</body>
</html>
```